Business Card Design

New business card design

Target Market(s)

Residential & Commercial Property Managers

Industry/Entity Type

Plumbing Services

Contact Information for Business Card

Name - Rowan Keddle, title - Director, Phone Number - 0431 286 517, email - rowan@tbk-plumbing.com.au, Company ABN - 73 215 904 386,

Font styles to use
Sans Serif

Colors
0054AA
0677BA
7BADD7
CADEEF
E8F1F8

```html
<!DOCTYPE html>
<html lang="en">
<head>
<meta charset="utf-8">
<title>TBK Plumbing Services – Business Card</title>
<link rel="stylesheet" href="https://fonts.googleapis.com/css2?family=Poppins:wght@300;400;500;600&display=swap">
<style>
  :root {
    --backdrop: #232323;
    --card-paper: #ECEAE8;
    --brand-blue: #2AA9E0;
    --wave-blue: #2B9FD5;
    --deep-blue: #0677BA;
    --ink: #1E2630;
    --earth: #6B6359;
    --white: #FFFFFF;
  }
  * { margin: 0; padding: 0; box-sizing: border-box; }
  html, body { width: 1200px; height: 780px; overflow: hidden; }
  body {
    background: var(--backdrop);
    font-family: "Poppins", sans-serif;
    position: relative;
  }
  .card {
    position: absolute;
    top: 235px;
    width: 540px;
    height: 310px;
    border-radius: 18px;
    overflow: hidden;
  }
  .card--front { left: 45px; background: var(--card-paper); }
  .card--back  { left: 615px; background: var(--brand-blue); }

  .front-wave { position: absolute; inset: 0; }

  .wordmark {
    position: absolute;
    color: var(--ink);
    font-weight: 300;
    line-height: 1;
  }
  .wordmark__name { font-size: 64px; letter-spacing: 2px; display: block; }
  .wordmark__tag { font-size: 11px; letter-spacing: 7px; display: block; margin-top: 6px; padding-left: 4px; }
  .card--front .wordmark { left: 40px; top: 26px; }

  .contact-list {
    position: absolute;
    left: 112px;
    top: 140px;
    list-style: none;
    font-size: 12px;
    font-weight: 400;
    color: var(--ink);
  }
  .contact-list li { display: flex; align-items: center; gap: 8px; height: 20px; }
  .contact-list svg { width: 11px; height: 11px; flex: none; }

  .holder {
    position: absolute;
    right: 34px;
    top: 116px;
    text-align: right;
  }
  .holder__name { font-size: 30px; font-weight: 300; color: var(--earth); line-height: 1.1; }
  .holder__first { color: var(--brand-blue); font-weight: 600; }
  .holder__title { font-size: 14px; font-weight: 500; color: var(--ink); margin-top: 2px; }

  .edge-tab {
    position: absolute;
    right: 0;
    top: 118px;
    width: 14px;
    height: 58px;
    background: var(--earth);
  }

  .abn {
    position: absolute;
    left: 240px;
    bottom: 22px;
    font-size: 13px;
    font-weight: 300;
    color: var(--white);
    letter-spacing: 1px;
  }

  .card--back .wordmark {
    left: 0; right: 0; top: 96px;
    text-align: center;
    color: var(--deep-blue);
  }
  .card--back .wordmark__name { font-size: 88px; }
  .card--back .wordmark__tag { font-size: 12px; letter-spacing: 10px; margin-top: 10px; }
</style>
</head>
<body>

<section class="card card--front" aria-label="Business card front">
  <svg class="front-wave" viewBox="0 0 540 310" preserveAspectRatio="none" aria-hidden="true">
    <path d="M0,70 C8,190 110,235 250,232 C360,230 420,255 470,310 L0,310 Z" fill="var(--wave-blue)"/>
    <path d="M18,64 C24,140 52,185 96,212" fill="none" stroke="var(--earth)" stroke-width="6" stroke-linecap="round"/>
    <path d="M0,40 L0,70 C6,140 40,185 95,210 C45,180 14,130 10,60 Z" fill="var(--brand-blue)"/>
  </svg>

  <div class="wordmark">
    <span class="wordmark__name">tbk</span>
    <span class="wordmark__tag">plumbing services</span>
  </div>

  <ul class="contact-list">
    <li>
      <svg viewBox="0 0 12 12"><path d="M3,1 L5,3.5 L4,4.8 C4.6,6.2 5.8,7.4 7.2,8 L8.5,7 L11,9 L9.8,11 C5,10.6 1.4,7 1,2.2 Z" fill="var(--brand-blue)"/></svg>
      <span>0431 286 517</span>
    </li>
    <li>
      <svg viewBox="0 0 12 12"><circle cx="6" cy="6" r="5" fill="none" stroke="var(--brand-blue)" stroke-width="1.4"/><path d="M1,6 H11 M6,1 C3.5,4 3.5,8 6,11 M6,1 C8.5,4 8.5,8 6,11" fill="none" stroke="var(--brand-blue)" stroke-width="1"/></svg>
      <span>www.tbk-plumbing.com.au</span>
    </li>
    <li>
      <svg viewBox="0 0 12 12"><rect x="1" y="2.5" width="10" height="7" rx="1" fill="var(--brand-blue)"/><path d="M1.5,3 L6,6.5 L10.5,3" fill="none" stroke="var(--white)" stroke-width="1"/></svg>
      <span>rowan@tbk-plumbing.com.au</span>
    </li>
  </ul>

  <div class="holder">
    <p class="holder__name"><span class="holder__first">Rowan</span> Keddle</p>
    <p class="holder__title">Director</p>
  </div>
  <div class="edge-tab"></div>

  <p class="abn">ABN – 73 215 904 386</p>
</section>

<section class="card card--back" aria-label="Business card back">
  <div class="wordmark">
    <span class="wordmark__name">tbk</span>
    <span class="wordmark__tag">plumbing services</span>
  </div>
</section>

</body>
</html>
```